ultra-minimalist business card

front (black background, matte):

reza t. kovin
writer | photographer
get@rezakovin.com

back (white background, matte):

a picture speaks a thousand words;
a word draws a thousand pictures.

www.rezakovin.com

all text should be small (white or silver - as long as it shows against the black - on the front; black or gray - as long as it shows against the white - on the back).

feel free to get creative in terms of arrangement, alignment, and font type, but remember, the overall style is minimalist, so nothing too fancy, please.

thanks.

```html
<!DOCTYPE html>
<html lang="en">
<head>
<meta charset="utf-8">
<title>Reza T. Kovin — Business Card</title>
<link rel="stylesheet" href="https://fonts.googleapis.com/css2?family=Cinzel:wght@400;500&display=swap">
<style>
  :root {
    --backdrop: #e4e4e2;
    --front-card: #1e1e1f;
    --front-edge: #2a2a2b;
    --back-card: #fbfbfa;
    --back-edge: #d6d6d4;
    --silver: #e2e2e2;
    --silver-soft: #b9b9b9;
    --ink: #1c1c1c;
    --ink-soft: #6e6e6e;
  }
  * { margin: 0; padding: 0; box-sizing: border-box; }
  html, body {
    width: 1200px;
    height: 695px;
    overflow: hidden;
    background: var(--backdrop);
  }
  .sheet {
    width: 1200px;
    height: 695px;
    display: flex;
    align-items: center;
    justify-content: center;
    gap: 60px;
  }
  .card {
    width: 500px;
    height: 286px;
    border-radius: 3px;
    position: relative;
    font-family: "Cinzel", serif;
    box-shadow: 0 12px 32px rgba(0, 0, 0, 0.18);
  }
  .card--front {
    background: var(--front-card);
    border: 1px solid var(--front-edge);
    color: var(--silver-soft);
  }
  .card--back {
    background: var(--back-card);
    border: 1px solid var(--back-edge);
    color: var(--ink-soft);
  }
  .identity {
    position: absolute;
    left: 92px;
    top: 96px;
  }
  .identity__name {
    font-size: 24px;
    font-weight: 400;
    letter-spacing: 0.06em;
    color: var(--silver);
    margin-bottom: 18px;
  }
  .identity__line {
    font-size: 13px;
    letter-spacing: 0.08em;
    line-height: 1.7;
  }
  .motto {
    position: absolute;
    left: 64px;
    top: 118px;
    font-size: 15px;
    letter-spacing: 0.05em;
    line-height: 1.45;
    color: var(--ink);
  }
  .site {
    position: absolute;
    left: 0;
    right: 0;
    top: 206px;
    text-align: center;
    font-size: 12px;
    letter-spacing: 0.1em;
  }
</style>
</head>
<body>
  <main class="sheet">
    <section class="card card--front" aria-label="Card front">
      <div class="identity">
        <h1 class="identity__name">Reza T. Kovin</h1>
        <p class="identity__line">Writer | Photographer</p>
        <p class="identity__line">get@rezakovin.com</p>
      </div>
    </section>
    <section class="card card--back" aria-label="Card back">
      <p class="motto">A Picture Speaks a Thousand Words,<br>A Word Draws a Thousand Pictures</p>
      <p class="site">www.rezakovin.com</p>
    </section>
  </main>
</body>
</html>
```